Norvane Freight and Provision Service Brochure

Please see http://www.norvanefreight.example for who we are and what we do.
We would like to see a design that matches the industry we work in i.e. Oil and Gas. The design should communicate large, heavy field operations, supply of vast bulk fuel quantities to our US and Afghan Military customers, plus financial independence and the companies whatever it takes attitude operation in remote often hostile areas. Dark colors like on the website - contrasting our green logo. A strong focus on our past performance/past experience.

Target Market(s)

Military Customers, Partners, Subcontractors

Industry/Entity Type

Industry

Contact Information for Business Card

Display of Address, Phone, email etc. of our 4 offices

Font styles to use
Sans Serif

Requirements
Must have
• Glossy brochure, modern, cool design. Great display (map) of our offices in the Middle East, Europe and Central Asia. A focus on our past performance/past experience. Customer logos/references
Nice to have
• Prominent highlighted watermark logo
Should not have
• Standard A4/Letter brochure

```html
<!DOCTYPE html>
<html lang="en">
<head>
<meta charset="utf-8">
<title>Norvane Freight and Provision – Service Brochure Spread</title>
<link href="https://fonts.googleapis.com/css2?family=Barlow:wght@400;500;600&display=swap" rel="stylesheet">
<style>
  :root {
    --lime: #8fe400;
    --leaf-text: #4d7d12;
    --navy: #1f2a6b;
    --ink: #333a3f;
    --frame: #9a9a9a;
    --paper: #ffffff;
  }
  * { margin: 0; padding: 0; box-sizing: border-box; }
  html, body { width: 1200px; height: 999px; overflow: hidden; background: var(--paper); }
  body { position: relative; font-family: "Barlow", Arial, sans-serif; color: var(--ink); }

  .page { position: absolute; top: 287px; width: 600px; height: 425px; border: 1px solid var(--frame); background: var(--paper); overflow: hidden; }
  .page--left { left: 0; }
  .page--right { left: 600px; }

  .photo { position: absolute; }
  .photo--platform-night { left: 0; top: 0; width: 258px; height: 153px; background: linear-gradient(180deg, #2a34a8 0%, #3b45b8 45%, #6d5a3a 70%, #2c2a35 100%); }
  .photo--sunset-field { left: 258px; top: 0; width: 342px; height: 153px; background: linear-gradient(180deg, #5a4a30 0%, #c8902e 40%, #e8b045 62%, #3a2e1c 82%, #1c1810 100%); }
  .photo--storage-tanks { left: 0; top: 209px; width: 440px; height: 216px; background: linear-gradient(90deg, rgba(150,160,165,1) 0%, rgba(200,205,205,1) 45%, rgba(255,255,255,0) 100%), linear-gradient(180deg, #b9c6cf 0%, #e4e6e4 60%, #9a8a80 100%); -webkit-mask-image: linear-gradient(90deg, #000 60%, transparent 100%); mask-image: linear-gradient(90deg, #000 60%, transparent 100%); }

  .section-band { position: absolute; left: 0; top: 153px; width: 260px; height: 56px; background: var(--lime); color: #fff; padding: 7px 0 0 40px; }
  .section-band__title { font-weight: 600; font-size: 14px; letter-spacing: 0.3px; line-height: 16px; }
  .section-band__sub { font-size: 10px; line-height: 12px; letter-spacing: 0.2px; }

  .intro { position: absolute; left: 292px; top: 207px; width: 270px; font-size: 14.5px; line-height: 17.2px; color: var(--leaf-text); }

  .folio { position: absolute; top: 392px; width: 19px; height: 31px; background: var(--lime); color: #fff; font-size: 7px; text-align: center; line-height: 31px; }
  .page--left .folio { left: 539px; }
  .page--right .folio { left: 539px; }

  .service { position: absolute; left: 121px; width: 440px; }
  .service h2 { font-size: 9px; font-weight: 600; color: var(--navy); line-height: 12px; margin-bottom: 1px; }
  .service p { font-size: 6.6px; line-height: 9.3px; color: var(--ink); margin-bottom: 6px; }
  .service--land { top: 40px; }
  .service--storage { top: 139px; }
  .service--fuelling { top: 245px; }
  .service--labs { top: 325px; }

  .icon { position: absolute; left: 38px; }
  .icon--truck { top: 40px; }
  .icon--storage { top: 140px; }
  .icon--fuelling { top: 245px; }
  .icon--labs { top: 322px; }

  .page-label { position: absolute; top: 748px; font-size: 25px; color: #111; font-family: Arial, sans-serif; }
  .page-label--left { left: 313px; }
  .page-label--right { left: 844px; }
</style>
</head>
<body>

<section class="page page--left">
  <div class="photo photo--platform-night" role="img" aria-label="Offshore oil platform lit at dusk against a deep blue sky"></div>
  <div class="photo photo--sunset-field" role="img" aria-label="Silhouetted drilling rigs at sea under a golden sunset sky"></div>
  <div class="section-band">
    <div class="section-band__title">WHAT WE OFFER</div>
    <div class="section-band__sub">FUEL DISTRIBUTION LOGISTICS<br>&amp; SERVICES</div>
  </div>
  <div class="photo photo--storage-tanks" role="img" aria-label="White spherical fuel storage tanks with steel stairways and pipework"></div>
  <p class="intro">By truly understanding the regions in which we work in, our Operations and Fuel Distribution Logistics Teams design implement and operate complex, fuel distribution networks allowing us to offer our customers full turn-key services, all the way from the pipeline to the gas tank.</p>
  <div class="folio">4</div>
</section>

<section class="page page--right">
  <svg class="icon icon--truck" width="74" height="46" viewBox="0 0 74 46" aria-hidden="true">
    <rect x="8" y="2" width="58" height="28" fill="var(--lime)"/>
    <g fill="#fff"><rect x="14" y="6" width="3" height="20"/><rect x="21" y="6" width="3" height="20"/><rect x="28" y="6" width="3" height="20"/><rect x="35" y="6" width="3" height="20"/><rect x="42" y="6" width="3" height="20"/><rect x="49" y="6" width="3" height="20"/><rect x="56" y="6" width="3" height="20"/></g>
    <rect x="2" y="30" width="70" height="7" fill="var(--navy)"/>
    <g fill="#fff"><circle cx="12" cy="33.5" r="2"/><circle cx="20" cy="33.5" r="2"/><circle cx="50" cy="33.5" r="2"/><circle cx="58" cy="33.5" r="2"/></g>
    <rect x="2" y="40" width="70" height="3" fill="var(--lime)"/>
  </svg>
  <svg class="icon icon--storage" width="74" height="56" viewBox="0 0 74 56" aria-hidden="true">
    <path d="M8 26 q-6 8 0 12 q6 -4 0 -12z" fill="none" stroke="var(--navy)" stroke-width="2"/>
    <path d="M18 18 q-4 6 0 9 q4 -3 0 -9z" fill="none" stroke="var(--navy)" stroke-width="2"/>
    <rect x="38" y="4" width="12" height="36" rx="5" fill="var(--lime)"/>
    <rect x="52" y="14" width="10" height="26" rx="4" fill="var(--lime)"/>
    <ellipse cx="30" cy="38" rx="12" ry="8" fill="var(--lime)"/>
    <rect x="4" y="44" width="66" height="8" fill="var(--lime)"/>
  </svg>
  <svg class="icon icon--fuelling" width="60" height="52" viewBox="0 0 60 52" aria-hidden="true">
    <circle cx="34" cy="32" r="18" fill="var(--lime)"/>
    <g fill="#fff"><rect x="22" y="26" width="22" height="3"/><rect x="22" y="32" width="18" height="3"/><rect x="22" y="38" width="14" height="3"/></g>
    <path d="M4 22 L22 4" stroke="var(--lime)" stroke-width="5" stroke-linecap="round"/>
    <path d="M33 6 q-5 7 0 10 q5 -3 0 -10z" fill="var(--navy)"/>
  </svg>
  <svg class="icon icon--labs" width="64" height="56" viewBox="0 0 64 56" aria-hidden="true">
    <path d="M6 6 q-5 7 0 10 q5 -3 0 -10z" fill="none" stroke="var(--navy)" stroke-width="2"/>
    <path d="M16 0 q-4 6 0 9 q4 -3 0 -9z" fill="none" stroke="var(--navy)" stroke-width="2"/>
    <path d="M14 18 h10 v8 a14 14 0 1 1 -10 0z" fill="var(--lime)"/>
    <path d="M40 4 h10 v18 l12 30 h-34 l12 -30z" fill="var(--lime)"/>
    <rect x="37" y="2" width="16" height="3" fill="var(--lime)"/>
  </svg>

  <div class="service service--land">
    <h2>Reliable Land Fuel Distribution Logistics</h2>
    <p>Since its founding Norvane has grown its fleet to more than 850 fuel-tanker trucks. Unlike most other companies Norvane owns the vehicle directly and operates them with its own highly trained driver personnel resulting in fast and direct access to information in the daily operations. Our strict preventative maintenance program allows us to compete as a leader in the industry with regards to dependability and professionalism. Norvane's in house maintenance facilities are company owned and operated, servicing hundreds of trucks from anything from minor maintenance such as air/fuel filters to major mechanical overhauls of engines and transmissions for any older asset in need of upgrade. In addition to our own fuel trucking capabilities and reliable supply at competitive fuel prices, we provide local market expertise in our network of leading regional companies, and a full spectrum of land fuel products, fuel services and fuel logistics solutions.</p>
  </div>

  <div class="service service--storage">
    <h2>State of the art Fuel Storage Facilities</h2>
    <p>Norvane's strategic, intermediate or destination fuel storage facilities are strategically located at border crossings at the main entry/border crossing points for bulk fuel along the various supply chains corridors. Our other main storage capacities in capital cities enable us to minimise the risk of disruption and to meet our customers' requirements for one time delivery and fuel storage needs.</p>
    <p>Most of these facilities are company owned and operated, while others are leased from the commercial market. For any solution, we ensure that the operations of the storage facility are in accordance with global best practice to ensure safety, security, environmental, quality requirements of the most rigid international API standards what guarantees that product quality is maintained at all times.</p>
  </div>

  <div class="service service--fuelling">
    <h2>Into-Plane &amp; Ground Fuelling</h2>
    <p>We provide our customers with safe, efficient, full scale refuel and defuel of all types of rotary and fixed-wing aircrafts on apron in accordance with the highest industry standards on Health, Safety and Environment. Our policies and procedures have been developed in accordance with the Air Transport Association (ATA) 103 Specification and the Joint Inspection Group (JIG) Guidelines for Aviation Fuel Quality Control &amp; Operating Procedures. We also provide into-vehicle, into-generator and other ground refuelling services including all aspects of fuel dispensing and management. As part of a turn-key solution, we provide these services wherever they may be required, including our customers' operational sites.</p>
  </div>

  <div class="service service--labs">
    <h2>Laboratories</h2>
    <p>Norvane's fuel test laboratories test diverse fuels for full quality specifications, and follow regulatory standards such as ASTM, ISO, and IP standards. In-house expertise and analytical resources support our operations and guarantees Norvane's customers full integrity of the products and highest quality product.. Norvane own fuel laboratories operate at world-class standards all over the region, supporting our operations from refinery, pipeline, terminal, and other operations.</p>
  </div>

  <div class="folio">5</div>
</section>

<div class="page-label page-label--left">Page 4</div>
<div class="page-label page-label--right">Page 5</div>

</body>
</html>
```